Fenwick Grading LTD - website for irrigation & Landscape Lighting & Buried service wire

Looking for a website to help promote my business with Irrigation (installation, service, etc) and buried service wire/drainage solutions.

Commercial/Residential

Landscape lighting.

I’ll get photos in the trucks and trailers to upload as well maybe the machine as well.

Target Market(s)

Homeowners who want green grass and beautiful gardens. Beautiful landscape lighting

Industry/Entity Type

Irrigation systems and landscape lighting and buried service wire to homes and offering Drainage soltions.

Coding

Coded - Design and coding required

Number of Pages Required

4 page

Colors
F0912C
F2A743
F7CA91
FBE8D2
FDF5EE

Requirements
Must have
• was hoping to link up my email on fenwickgrading@mailbox-example.net with the website if possible.
Nice to have
• Page for Irrigation, page for landscape lighting, page buried service wire & drainage soltions.

```html
<!DOCTYPE html>
<html lang="en">
<head>
<meta charset="utf-8">
<title>Fenwick Grading LTD</title>
<link href="https://fonts.googleapis.com/css2?family=Outfit:wght@400;500;600;700&family=Oswald:wght@500&display=swap" rel="stylesheet">
<style>
:root{
  --orange:#F0912C;--orange-2:#F2A743;--orange-3:#F7CA91;--cream:#FBE8D2;--cream-2:#FDF5EE;
  --ink:#1c1c1c;--text:#444;--muted:#888;--grey-bg:#f3f3f3;--dark:#1b1b1b;--white:#fff;
}
*{box-sizing:border-box;margin:0;padding:0}
html,body{width:1200px;height:5343px;overflow:hidden}
body{font-family:"Outfit",sans-serif;color:var(--ink);background:var(--white);position:relative}
section,header,footer{position:absolute;left:0;width:1200px}
.btn{display:inline-block;background:var(--orange);color:var(--white);font-size:11px;font-weight:600;padding:11px 17px;border-radius:3px;text-decoration:none}
.sec-title{text-align:center;font-size:36px;font-weight:600;color:var(--ink)}
.sec-title::after{content:"";display:block;width:60px;height:3px;background:var(--orange);margin:16px auto 0}
.photo{position:absolute}
/* hero */
.hero{top:0;height:601px}
.hero .photo{inset:0;background:radial-gradient(ellipse at 50% 80%,#6b5a2a 0%,#2f3a1e 35%,#141a12 75%)}
.hero .shade{position:absolute;inset:0;background:rgba(0,0,0,.25)}
.brand{position:absolute;left:141px;top:42px;display:flex;align-items:center;gap:10px;color:var(--white);font-size:20px;font-weight:600;width:160px;line-height:1.1}
.brand .mark{width:14px;height:14px;background:var(--orange);flex:none}
.hero .top-btn{position:absolute;right:142px;top:19px}
.nav{position:absolute;top:86px;right:142px;display:flex;gap:34px;font-size:12px;font-weight:500;color:var(--white);white-space:nowrap}
.hero-copy{position:absolute;top:228px;left:0;width:1200px;text-align:center;color:var(--white)}
.hero-copy h1{font-family:"Oswald",sans-serif;font-weight:500;font-size:36px;line-height:49px}
.hero-copy p{font-size:13px;line-height:22px;margin:10px auto 12px;width:700px}
/* services */
.services{top:601px;height:674px}
.services .sec-title{margin-top:52px}
.services .lead{text-align:center;font-size:15px;line-height:27px;color:var(--text);width:650px;margin:18px auto 0}
.card{position:absolute;background:var(--white);box-shadow:0 3px 12px rgba(0,0,0,.08);border-radius:3px}
.card .photo{left:0;top:0;width:266px;height:212px;position:relative}
.card h3{font-size:17px;font-weight:600;margin:28px 0 0 20px;white-space:nowrap}
.card .more{display:inline-block;color:var(--orange);font-size:13px;margin:16px 0 0 20px;border-bottom:2px solid var(--orange);padding-bottom:4px}
.card p{font-size:12px;line-height:20px;color:var(--text);margin:10px 20px 0}
/* about */
.about{top:1275px;height:628px}
.about .photo{inset:0;background:linear-gradient(180deg,#4a5d3c 0%,#7a8066 40%,#3c6a23 70%,#4f8a2a 100%)}
.about-panel{position:absolute;left:607px;top:83px;width:452px;height:456px;background:rgba(18,18,18,.9);border-radius:8px;color:var(--white);padding:52px 42px}
.about-panel h4{font-size:19px;font-weight:600}
.about-panel h2{font-size:32px;font-weight:500;margin:10px 0 26px}
.about-panel p{font-size:11.5px;line-height:20.5px;color:#ddd;margin-bottom:12px}
/* video */
.video{top:1903px;height:678px}
.video .sec-title{margin-top:78px}
.player{position:absolute;left:191px;top:176px;width:812px;height:404px;border-radius:8px;overflow:hidden;box-shadow:0 14px 28px rgba(0,0,0,.25)}
.player .photo{inset:0;background:radial-gradient(ellipse at 50% 70%,#7a6a3a 0%,#34431f 40%,#111 85%)}
.bar{position:absolute;left:10px;right:10px;bottom:12px;height:20px;display:flex;align-items:center;gap:8px}
.bar .play{width:38px;height:20px;background:var(--orange);border-radius:3px}
.bar .track{flex:1;height:3px;background:rgba(255,255,255,.4)}
/* reviews */
.reviews{top:2581px;height:539px;background:var(--grey-bg)}
.reviews .sec-title{margin-top:78px}
.review{position:absolute;top:193px;width:434px;height:257px;background:var(--white);text-align:center;padding-top:65px;box-shadow:0 3px 10px rgba(0,0,0,.05)}
.review::after{content:"";position:absolute;left:22px;right:22px;bottom:-4px;height:5px;background:var(--orange);border-radius:3px}
.avatar{position:absolute;top:-34px;left:50%;margin-left:-38px;width:76px;height:76px;border-radius:50%;border:3px solid var(--orange);background:linear-gradient(#c99f7e,#7b5a45)}
.review h3{font-size:17px;font-weight:600}
.review p{font-size:12px;line-height:20.5px;color:var(--text);width:360px;margin:18px auto 0}
.arrow{position:absolute;top:2882px;width:20px;height:20px;border-radius:50%;background:var(--white);box-shadow:0 1px 4px rgba(0,0,0,.2)}
/* gallery */
.gallery{top:3120px;height:794px}
.gallery .sec-title{margin-top:74px}
.grid{position:absolute;left:141px;top:170px;display:grid;grid-template-columns:repeat(4,225px);grid-auto-rows:226px;gap:8px 6px}
.grid div{border-radius:2px}
.gallery .btn{position:absolute;left:508px;top:668px}
/* cta */
.cta{top:3914px;height:398px;color:var(--white);text-align:center}
.cta .photo{inset:0;background:linear-gradient(180deg,#1e2a1c,#2f4a22 60%,#3c5f28)}
.cta .shade{position:absolute;inset:0;background:rgba(0,0,0,.35)}
.cta-copy{position:relative;padding-top:98px}
.cta-copy h2{font-size:30px;font-weight:500;line-height:42px}
.cta-copy p{font-size:12px;line-height:21px;width:660px;margin:18px auto 18px}
/* contact */
.contact{top:4312px;height:643px}
.form-card{position:absolute;left:228px;top:93px;width:746px;height:421px;background:var(--white);box-shadow:0 2px 16px rgba(0,0,0,.1);text-align:center;padding-top:52px}
.form-card h2{font-size:32px;font-weight:600}
.form-card .sub{font-size:12px;color:var(--text);margin-top:6px}
.field{position:absolute;height:41px;border:1px solid #e4e4e4;background:#fafafa;display:flex;align-items:center;font-size:11px;color:#666;text-align:left}
.field .ico{width:40px;height:100%;border-right:1px solid #e4e4e4;display:flex;align-items:center;justify-content:center;margin-right:10px}
.submit{position:absolute;left:56px;width:638px;height:41px;background:var(--orange);color:var(--white);font-size:12px;font-weight:600;display:flex;align-items:center;justify-content:center}
/* footer */
footer{top:4955px;height:388px;background:var(--dark);color:var(--white)}
.footer-brand{position:absolute;left:0;width:1200px;top:78px;text-align:center;font-size:26px;font-weight:600}
.footer-brand .mark{display:inline-block;width:14px;height:14px;background:var(--orange);margin-right:10px;vertical-align:middle}
.fnav{position:absolute;top:198px;left:0;width:1200px;display:flex;justify-content:center;gap:42px;font-size:11.5px;font-weight:500;white-space:nowrap}
.finfo{position:absolute;top:262px;display:flex;gap:12px;align-items:center;font-size:12px;line-height:19px}
.ficon{width:34px;height:34px;border-radius:50%;border:1px solid #ddd;display:flex;align-items:center;justify-content:center}
.copy{position:absolute;left:141px;top:345px;font-size:11px;color:#ccc}
.social{position:absolute;left:900px;top:337px;display:flex;gap:9px}
.social span{width:32px;height:32px;border-radius:50%;border:1px solid #ddd}
</style>
</head>
<body>

<section class="hero">
  <div class="photo" role="img" aria-label="Night garden with warm landscape lights and a footbridge among trees"></div>
  <div class="shade"></div>
  <div class="brand"><span class="mark"></span>Fenwick Grading LTD</div>
  <a class="btn top-btn">Free No Obligation Quote</a>
  <nav class="nav"><span>Home</span><span>Irrigation Systems</span><span>Landscape Lighting</span><span>Buried Wire &amp; Drainage</span><span>Contact Us</span></nav>
  <div class="hero-copy">
    <h1>Transform Your Outdoor Space With Our Expert<br>Irrigation And Lighting Solutions</h1>
    <p>Get the perfect blend of form and function with our state-of-the-art irrigation systems and landscape lighting. Trust our experienced team with buried service wire and drainage for your home</p>
    <a class="btn">Free No Obligation Quote</a>
  </div>
</section>

<section class="services">
  <h2 class="sec-title">Our Services</h2>
  <p class="lead">Lorem Ipsum is simply dummy text of the printing and typesetting industry. Lorem Ipsum has been the industry's standard dummy text ever since</p>
  <div class="card" style="left:141px;top:211px;width:282px;height:324px">
    <div class="photo" role="img" aria-label="Sprinkler watering a green lawn beside a stone border" style="background:linear-gradient(#cfd6c5,#6e9a3c 60%,#4d7a2a)"></div>
    <h3>Irrigation Systems</h3><span class="more">Learn More</span>
  </div>
  <div class="card" style="left:458px;top:211px;width:282px;height:376px">
    <div class="photo" role="img" aria-label="Lit garden path at dusk" style="background:radial-gradient(#a08a45,#2c3a1c 70%)"></div>
    <h3 style="margin-top:22px">Landscape Lighting</h3>
    <p>Enhance Your Outdoor Space with Beautiful &amp; Functional Lighting Solutions</p>
    <span class="more" style="margin-top:12px">Learn More</span>
  </div>
  <div class="card" style="left:776px;top:211px;width:282px;height:324px">
    <div class="photo" role="img" aria-label="Service wire and drain pipe laid in a trench" style="background:linear-gradient(135deg,#6b5a44,#8a7760 50%,#5d4a38)"></div>
    <h3>Buried Wire &amp; Drainage</h3><span class="more">Learn More</span>
  </div>
</section>

<section class="about">
  <div class="photo" role="img" aria-label="House with trimmed hedges and a green lawn"></div>
  <div class="about-panel">
    <h4>About</h4>
    <h2>Fenwick Grading LTD</h2>
    <p>Lorem ipsum dolor sit amet, consectetur adipiscing elit sed do eiusmod tempor incididunt ut labore et dolore magna aliqua Ut enim ad minim veniam quis</p>
    <p>Lorem ipsum dolor sit amet, consectetur adipiscing elit sed do eiusmod tempor incididunt ut labore et dolore magna aliqua Ut enim ad minim veniam quis "Lorem ipsum dolor sit amet, consectetur adipiscing elit sed do eiusmod tempor incididunt ut labore et dolore magna aliqua</p>
    <a class="btn" style="margin-top:10px">Free No Obligation Quote</a>
  </div>
</section>

<section class="video">
  <h2 class="sec-title">Watch Video</h2>
  <div class="player">
    <div class="photo" role="img" aria-label="Video still of a lit garden walkway at night"></div>
    <svg style="position:absolute;left:374px;top:180px" width="64" height="46" viewBox="0 0 64 46"><rect x="2" y="2" width="60" height="42" rx="10" fill="none" stroke="#fff" stroke-width="3"/><path d="M26 13v20l17-10z" fill="none" stroke="#fff" stroke-width="3"/></svg>
    <div class="bar"><span class="play"></span><span class="track"></span></div>
  </div>
</section>

<section class="reviews">
  <h2 class="sec-title">Customer Reviews</h2>
  <div class="review" style="left:143px">
    <div class="avatar" role="img" aria-label="Customer portrait"></div>
    <h3>Marcus Hale</h3>
    <p>Lorem Ipsum is simply dummy text of the printing and typesetting industry. Lorem Ipsum has been the industry's standard dummy text ever since the 1500s, when an unknown printer took a galley of type and scrambled standard dummy text ever since</p>
  </div>
  <div class="review" style="left:624px">
    <div class="avatar" role="img" aria-label="Customer portrait"></div>
    <h3>Dana Ruiz</h3>
    <p>Lorem Ipsum is simply dummy text of the printing and typesetting industry. Lorem Ipsum has been the industry's standard dummy text ever since the 1500s, when an unknown printer took a galley of type and scrambled standard dummy text ever since</p>
  </div>
</section>
<span class="arrow" style="left:133px"></span>
<span class="arrow" style="left:1048px"></span>

<section class="gallery">
  <h2 class="sec-title">Project Gallery</h2>
  <div class="grid">
    <div role="img" aria-label="Lit patio at night" style="background:linear-gradient(#222,#3a4a2a)"></div>
    <div role="img" aria-label="Sprinklers on lawn" style="background:linear-gradient(#c9b48a,#5f8a2e)"></div>
    <div role="img" aria-label="Technician working on a wall box" style="background:linear-gradient(#5a4a3a,#2a2320)"></div>
    <div role="img" aria-label="Yellow house with lawn" style="background:linear-gradient(#8fb3d6,#d8c38a 50%,#6a9a3a)"></div>
    <div role="img" aria-label="Sprinkler head close-up" style="background:linear-gradient(#8dbf4a,#3f7a22)"></div>
    <div role="img" aria-label="Cables in soil with shovel" style="background:linear-gradient(#5a4a3a,#7a6650)"></div>
    <div role="img" aria-label="Lit gazebo at night" style="background:linear-gradient(#1d1d1d,#5a3e1e)"></div>
    <div role="img" aria-label="Lawn sprinklers by a house" style="background:linear-gradient(#3b4a5a,#5f8a30)"></div>
  </div>
  <a class="btn">Free No Obligation Quote</a>
</section>

<section class="cta">
  <div class="photo" role="img" aria-label="Garden path lined with hedges and lights"></div>
  <div class="shade"></div>
  <div class="cta-copy">
    <h2>Expertise In Irrigation Systems, Landscape<br>Lighting, Buried Service Wire And Drainage</h2>
    <p>Lorem ipsum dolor sit amet, consectetuer adipiscing elit, sed diam nonummy nibh euismod tincidunt ut laoreet dolore magna aliquam erat volutpat. Ut wisi enim ad minim veniam, quis nostrud exerci tation.</p>
    <a class="btn">Contact Us</a>
  </div>
</section>

<section class="contact">
  <div class="form-card">
    <h2>Contact Us</h2>
    <p class="sub">Lorem ipsum dolor sit amet consectetuer adipiscing elit</p>
    <div class="field" style="left:56px;top:148px;width:312px"><span class="ico"><svg width="12" height="12"><circle cx="6" cy="4" r="3" fill="#bbb"/><rect x="1" y="8" width="10" height="4" rx="2" fill="#bbb"/></svg></span>First Name*</div>
    <div class="field" style="left:382px;top:148px;width:312px"><span class="ico"><svg width="12" height="12"><path d="M1 6l10-5-3 10-2-4z" fill="#bbb"/></svg></span>Email Address*</div>
    <div class="field" style="left:56px;top:204px;width:312px"><span class="ico"><svg width="12" height="12"><path d="M2 1l3 1 0 3-1 1c1 2 2 3 4 4l1-1 3 0 0 3c-6 0-10-5-10-11z" fill="#bbb"/></svg></span>Telephone*</div>
    <div class="field" style="left:382px;top:204px;width:312px"><span class="ico"><svg width="12" height="12"><rect x="1" y="1" width="10" height="10" fill="none" stroke="#bbb"/></svg></span>Inquiry For*</div>
    <div class="field" style="left:56px;top:260px;width:638px;height:80px;align-items:flex-start"><span class="ico" style="height:40px;border:none"><svg width="12" height="12"><rect x="1" y="2" width="10" height="7" rx="2" fill="#bbb"/></svg></span><span style="padding-top:13px">Messages</span></div>
    <div class="submit" style="top:361px">Submit Now</div>
  </div>
</section>

<footer>
  <svg style="position:absolute;left:0;top:-20px" width="1200" height="22"><path d="M0 22L600 0L1200 22Z" fill="var(--orange)"/><path d="M0 22L600 4L1200 22Z" fill="var(--dark)"/></svg>
  <div class="footer-brand"><span class="mark"></span>Fenwick Grading LTD</div>
  <nav class="fnav"><span>Home</span><span>Irrigation Systems</span><span>Landscape Lighting</span><span>Buried Wire &amp; Drainage</span><span>Contact Us</span></nav>
  <div class="finfo" style="left:210px"><span class="ficon"><svg width="12" height="14"><path d="M6 13C2 8 1 6 1 5a5 5 0 0 1 10 0c0 1-1 3-5 8z" fill="#fff"/><circle cx="6" cy="5" r="2" fill="var(--dark)"/></svg></span><span>123, Building Name, Street<br>City, State XY 123456</span></div>
  <div class="finfo" style="left:527px"><span class="ficon"><svg width="12" height="12"><path d="M2 1l3 1 0 3-1 1c1 2 2 3 4 4l1-1 3 0 0 3c-6 0-10-5-10-11z" fill="#fff"/></svg></span><span>Phone<br>123-456-7890</span></div>
  <div class="finfo" style="left:769px"><span class="ficon"><svg width="12" height="10"><rect x="0" y="0" width="12" height="10" rx="1" fill="#fff"/><path d="M0 1l6 4 6-4" fill="none" stroke="var(--dark)"/></svg></span><span>E-Mail<br>info@fenwickgrading-example.net</span></div>
  <p class="copy">© 2024 Fenwick Grading LTD . All Rights Reserved.</p>
  <div class="social"><span></span><span></span><span></span><span></span></div>
</footer>

</body>
</html>
```